Web landing page design

- Create a Web Design (Uncoded - PSD layout only)

We need a single web page design to promote our service. This page will
acts as a landing page for users and also be utilized in social media
advertising. Please provide us with a cutting edge design. I have attached
a link for what the company is about. In essence we are a photo checking
service which reviews photos for retailers, hotels abd car dealerships to
check everything is good after a service has been performed. Whether it be
a new promotion, cleaning or just checking prices. I am looking for a
design to say that we do many photos and at a very cost effective price
(team based in Mexico)

Link: https://slidevault.example/view/qTr8nWx2LpZk4mHcYdJs/
*Deadline*
5 days
*Updates*

- The Start Here box needs to look like this:

-Start Here (heading)
-A box for email addresses to be entered
-Then a check box with "Yes, I have read and agree to the Privacy Policy
and agree to receive email marketing from Plumora88'
-A submit button

All of this information needs to be in one box please. And please feel
free to contact me if you have any questions about this.

*Target Market(s)*
Retail business, Merchandising companies, Rental property owners, Car
dealers
Updates

Please can you submit entries. I am just looking for a tidy to a presentation already created. Just needs design touches.

Target Market(s)

Ability for audience to understand concept quickly
Benefits to why to use the product stand out
Technology driven approach

Industry/Entity Type

Retail

Number of Pages Required

1 page

Colors
0792cd

Requirements
Must have
• Clean and modern design

```html
<!DOCTYPE html>
<html lang="en">
<head>
<meta charset="utf-8">
<title>Plumora88 – Transform Retail Execution</title>
<link href="https://fonts.googleapis.com/css2?family=Lato:wght@400;700;900&display=swap" rel="stylesheet">
<style>
:root{
  --brand:#0792cd;
  --brand-dark:#0b4fb8;
  --brand-light:#3a9be0;
  --ink:#333a40;
  --muted:#6b7378;
  --band:#e8e8e8;
  --tile:#f4f4f4;
  --white:#ffffff;
  --teal:#18a99a;
  --green:#2fa84f;
  --phone-edge:#c3d0d6;
  --screen-line:#d5dde2;
  --hero-a:#8a8f93;
  --hero-b:#4f5458;
}
*{box-sizing:border-box;margin:0;padding:0}
html,body{width:1200px;height:2941px;overflow:hidden}
body{font-family:'Lato',sans-serif;color:var(--ink);background:var(--white);position:relative}
.abs{position:absolute}

/* hero */
.hero{left:0;top:0;width:1200px;height:625px;background:linear-gradient(160deg,#b5b9bc 0%,var(--hero-a) 45%,var(--hero-b) 100%)}
.logo{left:122px;top:28px;display:flex;align-items:center;gap:12px;color:var(--white);font-size:34px;font-weight:700}
.logo-dot{width:44px;height:44px;border-radius:50%;background:var(--brand)}
.nav{top:44px;right:136px;display:flex;gap:62px}
.nav a{color:var(--white);text-decoration:none;font-size:19px;font-weight:700}
.hero-title{left:0;width:1200px;top:258px;text-align:center;color:var(--white);font-size:50px;font-weight:900;line-height:56px;text-transform:uppercase}

/* stats */
.stats{left:0;top:625px;width:1200px;height:155px;background:var(--band)}
.polaroid{background:linear-gradient(135deg,#7b7f86,#3e4a58);border:6px solid var(--white);box-shadow:0 2px 6px rgba(0,0,0,.25)}
.stat{top:42px;width:170px;text-align:center}
.stat b{display:block;color:var(--brand);font-size:30px;font-weight:400}
.stat span{display:block;font-size:10px;line-height:13px;color:var(--ink);text-transform:uppercase;margin-top:6px}
.divider{top:0;width:2px;height:155px;background:#d2d2d2}

/* phones */
.phones{left:102px;top:862px;width:562px;height:386px;display:flex;justify-content:space-between}
.phone{position:relative;width:182px;height:386px;border-radius:24px;background:#eef3f5;border:3px solid var(--phone-edge)}
.phone .speaker{position:absolute;left:70px;top:26px;width:36px;height:5px;border-radius:3px;background:#b5c1c7}
.phone .cam{position:absolute;left:88px;top:10px;width:7px;height:7px;border-radius:50%;background:#b5c1c7}
.phone .home{position:absolute;left:78px;bottom:12px;width:20px;height:20px;border-radius:5px;border:2px solid #b5c1c7}
.screen{position:absolute;left:8px;top:54px;width:160px;height:286px;background:var(--white);border:1px solid var(--screen-line);overflow:hidden;font-size:8.5px;line-height:11px}
.s-blue{color:#1a3fc4;font-weight:700;font-size:9.5px;line-height:11px;padding:6px 8px}
.s-teal{background:var(--teal);color:var(--white);height:34px;margin-top:42px;padding:12px 8px;font-size:9px}
.s-field{padding:8px 8px 0;color:#444}
.s-field b{display:block;font-weight:700;color:#222}
.s-big{font-size:15px;line-height:17px;font-weight:700;color:var(--green);padding:10px 8px}
.s-photo{margin:4px 8px;height:46px;background:linear-gradient(90deg,#c9332d,#8b2a3a 50%,#b9443a)}
.s-title{color:var(--teal);font-weight:700;font-style:normal;font-size:9.5px;text-align:center;padding:8px 0 6px}
.s-box{margin:0 8px;background:#e4e8ea;padding:4px 6px;font-weight:700;color:#222}
.s-row{display:flex;align-items:center;gap:6px;margin:6px 8px 0;padding-bottom:4px;border-bottom:1px solid var(--screen-line)}
.s-row i{width:16px;height:16px;border-radius:50%;background:var(--teal);flex:none}

/* features copy */
.feat-title{left:717px;top:842px;font-size:29px;font-weight:400}
.feat-sub{left:717px;top:888px;font-size:21px;color:var(--muted)}
.feat-copy{left:717px;top:930px;width:450px;font-size:13.5px;line-height:21px;color:var(--ink)}
.benefit{left:717px;display:flex;align-items:center;gap:16px;font-size:14px;line-height:20px;width:450px}
.benefit .ico{width:72px;height:72px;border-radius:50%;border:1.5px solid #b9c6d2;display:flex;align-items:center;justify-content:center;flex:none}

/* devices */
.monitor{left:455px;top:1384px;width:452px;height:312px;background:#1d1f22;border-radius:12px;padding:16px 16px 20px}
.monitor .display{width:100%;height:100%;background:var(--white);position:relative;overflow:hidden}
.m-bar{height:9px;background:#d4a514}
.m-table{position:absolute;left:8px;top:24px;width:235px;font-size:7.5px;color:#333;border-collapse:collapse}
.m-table th{text-align:left;font-weight:700;padding:3px 2px;border-bottom:1px solid #ccc}
.m-table td{padding:4px 2px;border-bottom:1px solid #e2e2e2;vertical-align:top;height:62px}
.m-thumb{width:40px;height:52px;background:linear-gradient(180deg,#3f4c7a,#b8464a)}
.m-map{position:absolute;left:250px;top:9px;right:0;bottom:0;background:linear-gradient(160deg,#e4ead8,#cfd9c2 60%,#b9cbd9)}
.stand-neck{left:620px;top:1696px;width:122px;height:48px;background:linear-gradient(180deg,#c9ccd0,#9fa4a9);clip-path:polygon(18% 0,82% 0,100% 100%,0 100%)}
.stand-base{left:600px;top:1742px;width:162px;height:10px;border-radius:3px;background:#b7bbbf}
.tablet{left:202px;top:1558px;width:334px;height:210px;background:#111;border-radius:16px;padding:14px 30px}
.tablet .display{width:100%;height:100%;background:var(--white);position:relative;overflow:hidden}
.t-head{position:absolute;left:24px;top:6px;font-size:7.5px;font-weight:700;text-align:center;width:110px}
.t-map{position:absolute;right:0;top:10px;width:80px;height:122px;background:linear-gradient(160deg,#d8dde2,#aab4be)}

/* upload band */
.upload{left:0;top:1830px;width:1200px;height:340px;background:linear-gradient(100deg,var(--brand-light),var(--brand-dark))}
.video{left:153px;top:52px;width:395px;height:233px;background:linear-gradient(135deg,#b98a6e,#6f5a56 60%,#9fa7b2)}
.play{left:164px;top:83px;width:68px;height:68px;border-radius:50%;border:3px solid var(--white)}
.upload h2{left:598px;top:64px;color:var(--white);font-size:24px;font-weight:400}
.upload ul{left:598px;top:110px;list-style:none;color:var(--white);font-size:18px}
.upload li{display:flex;align-items:center;gap:12px;height:56px}

/* brands */
.brands-title{left:0;width:1200px;top:2206px;text-align:center;color:var(--brand);font-size:29px;font-weight:400}
.brand-row{left:182px;top:2254px;width:840px;height:106px;background:var(--tile);display:flex;align-items:center;justify-content:space-around;padding:0 14px}
.brand{font-size:14px;font-weight:700;color:#555}
.arrow{top:2287px}

/* start here */
.start{left:0;top:2387px;width:1200px;height:408px;background:linear-gradient(160deg,#5a5048,#2e2a28 55%,#4c4640)}
.start h2{left:0;width:1200px;top:100px;text-align:center;color:var(--white);font-size:44px;font-weight:700}
.email{left:270px;top:178px;width:657px;height:62px;border-radius:31px;background:var(--white);border:5px solid rgba(255,255,255,.35);background-clip:padding-box;font-size:17px;color:#555;padding:15px 40px}
.consent{left:265px;top:260px;display:flex;align-items:center;gap:10px;color:var(--white);font-size:13px}
.consent i{width:17px;height:17px;border:1.5px solid var(--white);display:block}
.submit{left:539px;top:298px;width:130px;height:42px;border-radius:21px;background:var(--brand);color:var(--white);font-size:18px;text-align:center;line-height:42px}

/* footer */
.footer{left:0;top:2795px;width:1200px;height:146px;background:#e9e9e9}
.footer p{position:absolute;left:0;width:1200px;top:30px;text-align:center;font-size:13px;color:var(--ink)}
.social{position:absolute;left:502px;top:68px;width:198px;display:flex;justify-content:space-between}
.social span{width:34px;height:34px;border-radius:50%;background:#3f5a9a;display:block}
</style>
</head>
<body>

<header class="abs hero" role="img" aria-label="Photo: hand holding a phone photographing a retail shelf">
  <div class="abs logo"><span class="logo-dot"></span>Plumora88</div>
  <nav class="abs nav"><a>About</a><a>Results</a><a>How</a><a>Free Trial</a></nav>
  <h1 class="abs hero-title">Transform retail execution<br>with a simple photo</h1>
</header>

<section class="abs stats">
  <div class="abs polaroid" role="img" aria-label="Store photo" style="left:110px;top:48px;width:92px;height:74px;transform:rotate(-8deg)"></div>
  <div class="abs polaroid" role="img" aria-label="Store photo" style="left:198px;top:32px;width:86px;height:70px;transform:rotate(3deg)"></div>
  <div class="abs polaroid" role="img" aria-label="Store photo" style="left:265px;top:42px;width:90px;height:74px;transform:rotate(-4deg)"></div>
  <div class="abs stat" style="left:340px"><b>126,156</b><span>Photos verified<br>last month</span></div>
  <div class="abs divider" style="left:510px"></div>
  <div class="abs stat" style="left:518px"><b>15 cents</b><span>Per photo<br>reviewed</span></div>
  <div class="abs divider" style="left:685px"></div>
  <div class="abs stat" style="left:668px;width:205px"><b>1-8%</b><span>Sales increase with<br>improved compliance</span></div>
  <div class="abs polaroid" role="img" aria-label="Store photo" style="left:855px;top:42px;width:88px;height:74px;transform:rotate(-5deg)"></div>
  <div class="abs polaroid" role="img" aria-label="Store photo" style="left:930px;top:38px;width:86px;height:74px;transform:rotate(6deg)"></div>
  <div class="abs polaroid" role="img" aria-label="Store photo" style="left:1012px;top:30px;width:80px;height:74px;transform:rotate(-3deg)"></div>
</section>

<section>
  <div class="abs phones">
    <div class="phone"><span class="cam"></span><span class="speaker"></span>
      <div class="screen">
        <div class="s-blue">Report Completed Successfully<br>21/07/2017 16:30:46</div>
        <div class="s-teal">Visit Information</div>
        <div class="s-field"><b>Date</b>21/07/2017</div>
        <div class="s-field"><b>Rep</b>Area Team</div>
        <div class="s-field"><b>Retailer</b>Grovey</div>
        <div class="s-field"><b>Location</b>PLYMOUTH</div>
      </div>
      <span class="home"></span></div>
    <div class="phone"><span class="cam"></span><span class="speaker"></span>
      <div class="screen">
        <div class="s-big" style="display:flex;align-items:center;justify-content:space-between">Incorrect<br>Sequence<svg width="34" height="28" viewBox="0 0 34 28"><path d="M3 15l9 9L31 4" stroke="var(--green)" stroke-width="6" fill="none"/></svg></div>
        <div class="s-photo" role="img" aria-label="Photo of shelf products in the wrong order"></div>
      </div>
      <span class="home"></span></div>
    <div class="phone"><span class="cam"></span><span class="speaker"></span>
      <div class="screen">
        <div class="s-title">Key Insights - Portal</div>
        <div class="s-box">Trolley Bay 92% Attendance<br>89% Shelf Compliance</div>
        <div class="s-row"><i></i>Weather 12</div>
        <div class="s-row"><i></i>Range Refresh 17</div>
        <div class="s-row"><i></i>Display Missing 9</div>
        <div class="s-row"><i></i>Price Issues 14</div>
        <div class="s-title" style="padding:6px 0 2px">Trends</div>
        <svg style="display:block;margin:0 auto" width="120" height="56" viewBox="0 0 120 56"><rect x="4" y="30" width="6" height="22" fill="var(--teal)"/><rect x="13" y="38" width="6" height="14" fill="var(--teal)"/><rect x="22" y="44" width="6" height="8" fill="var(--teal)"/><circle cx="80" cy="28" r="24" fill="#dfe4e7"/><path d="M80 28V4a24 24 0 0 1 22 34z" fill="var(--teal)"/></svg>
      </div>
      <span class="home"></span></div>
  </div>

  <h2 class="abs feat-title">Plumora88 driving sales</h2>
  <p class="abs feat-sub">+ 3-8% Sales with strong compliance</p>
  <p class="abs feat-copy">Our clients demand field activities to be completed with provable accuracy, speed and factual insights. Our technology allows activities to be photographed, verified and corrective actions sent back to the shop floor at speed.</p>
  <div class="abs benefit" style="top:1040px"><span class="ico"><svg width="34" height="34" viewBox="0 0 34 34"><circle cx="17" cy="17" r="15" fill="var(--brand)"/><circle cx="17" cy="17" r="11" fill="#fff"/><path d="M17 10v7h5" stroke="var(--brand)" stroke-width="2.5" fill="none"/></svg></span>In Minutes verify national promotions<br>or range Changes</div>
  <div class="abs benefit" style="top:1128px"><span class="ico"><svg width="26" height="36" viewBox="0 0 26 36"><path d="M13 1C6 1 1 6 1 13c0 9 12 22 12 22s12-13 12-22C25 6 20 1 13 1z" fill="var(--brand)"/><circle cx="13" cy="13" r="5" fill="#fff"/></svg></span>Real time insights why locations are<br>not performing</div>
  <div class="abs benefit" style="top:1216px"><span class="ico"><svg width="34" height="26" viewBox="0 0 34 26"><rect width="34" height="26" rx="3" fill="var(--brand)"/><path d="M2 3l15 12L32 3" stroke="#fff" stroke-width="2.5" fill="none"/></svg></span>Eliminate field management audits,<br>email, calls with a digital workflow</div>

  <div class="abs monitor">
    <div class="display">
      <div class="m-bar"></div>
      <table class="m-table">
        <tr><th>Team</th><th>Postcode</th><th>Visit Date</th><th>Image</th></tr>
        <tr><td>North</td><td>0421</td><td>21/07/2017</td><td><div class="m-thumb" role="img" aria-label="Store photo"></div></td></tr>
        <tr><td>South</td><td>0427</td><td>21/07/2017</td><td><div class="m-thumb" role="img" aria-label="Store photo"></div></td></tr>
      </table>
      <div class="m-map" role="img" aria-label="Map with store visit markers"></div>
    </div>
  </div>
  <div class="abs stand-neck"></div>
  <div class="abs stand-base"></div>
  <div class="abs tablet">
    <div class="display">
      <div class="t-head">Week 28 Survey Report</div>
      <svg class="abs" style="left:8px;top:26px" width="180" height="120" viewBox="0 0 180 120">
        <rect x="4" y="70" width="9" height="40" fill="var(--teal)"/><rect x="16" y="76" width="9" height="34" fill="var(--teal)"/><rect x="28" y="82" width="9" height="28" fill="var(--teal)"/><rect x="40" y="90" width="9" height="20" fill="var(--teal)"/><rect x="52" y="98" width="9" height="12" fill="var(--teal)"/><rect x="64" y="102" width="9" height="8" fill="var(--teal)"/><rect x="76" y="105" width="9" height="5" fill="var(--teal)"/><rect x="88" y="106" width="9" height="4" fill="var(--teal)"/>
        <line x1="2" y1="111" x2="100" y2="111" stroke="#aaa"/>
        <circle cx="140" cy="34" r="20" fill="#dfe4e7"/><path d="M140 34V14a20 20 0 0 1 17 30z" fill="var(--teal)"/>
      </svg>
      <div class="t-map" role="img" aria-label="Map of survey locations"></div>
    </div>
  </div>
</section>

<section class="abs upload">
  <div class="abs video" role="img" aria-label="Video still: shopper in a store aisle">
    <span class="abs play"><svg width="62" height="62" viewBox="0 0 62 62"><path d="M24 18v26l20-13z" fill="#fff"/></svg></span>
  </div>
  <h2 class="abs">Upload the photo your way</h2>
  <ul class="abs">
    <li><svg width="24" height="24" viewBox="0 0 24 24"><circle cx="12" cy="12" r="12" fill="#fff"/><path d="M6 12l4 4 8-8" stroke="var(--brand)" stroke-width="2.5" fill="none"/></svg>Upload with our Digital Survey</li>
    <li><svg width="24" height="24" viewBox="0 0 24 24"><circle cx="12" cy="12" r="12" fill="#fff"/><path d="M6 12l4 4 8-8" stroke="var(--brand)" stroke-width="2.5" fill="none"/></svg>Upload to a drop box</li>
    <li><svg width="24" height="24" viewBox="0 0 24 24"><circle cx="12" cy="12" r="12" fill="#fff"/><path d="M6 12l4 4 8-8" stroke="var(--brand)" stroke-width="2.5" fill="none"/></svg>Utilize your photo capture system</li>
  </ul>
</section>

<section>
  <h2 class="abs brands-title">Serving Top Brands</h2>
  <svg class="abs arrow" style="left:140px" width="24" height="40" viewBox="0 0 24 40"><path d="M20 4L6 20l14 16" stroke="#888" stroke-width="4" fill="none"/></svg>
  <div class="abs brand-row">
    <span class="brand">Sevrano</span><span class="brand">Korvane</span><span class="brand">Haldris</span><span class="brand">Dunmere</span><span class="brand">Pellix</span><span class="brand">Hoskel</span><span class="brand">Merovin</span><span class="brand">Talbrecht</span><span class="brand">Larkmoor</span>
  </div>
  <svg class="abs arrow" style="left:1040px" width="24" height="40" viewBox="0 0 24 40"><path d="M4 4l14 16L4 36" stroke="#888" stroke-width="4" fill="none"/></svg>
</section>

<section class="abs start" role="img" aria-label="Photo: smiling woman using a laptop">
  <h2 class="abs">START HERE</h2>
  <div class="abs email">Your Email address</div>
  <div class="abs consent"><i></i>Yes, I have read and agree to the Privacy Policy and agree to receive email marketing from Plumora88</div>
  <div class="abs submit">Submit</div>
</section>

<footer class="abs footer">
  <p>© 2018 Company Name &nbsp;All right reserved &nbsp;Terms of Use</p>
  <div class="social" aria-label="Social links"><span></span><span style="background:#3a9fe0"></span><span style="background:#d6473a"></span><span style="background:#1f77b4"></span><span style="background:#d6332b"></span></div>
</footer>

</body>
</html>
```